Research and Innovation programme/projects in WOOD based industries

1.Pramenova s.r.o. (offical registered brand name of our company)
-Managing technology development projects
-International cooperation and development European projects
Our company was founded in 2008 and started to work as a counsilary company operating in the section of european funds administrated by Czech republic. Nowadays we are specializing on projects in the sphere of science and research co-financed by EU.Since 6.6.2013 we are registered under European comission for a purpose of broad support of transnational projects.

Target Market(s)

We are primarily focused on european companies, which stand behind the latest research and innovation of sawing, planing, glulam and logging technologies based on wooden materials.

Coding

Coded - Design and coding required

Number of Pages Required

5+ page

Font styles to use
Serif

Colors
cadf82
abd037
9bcb3c
fee18a
ffcf3e
ffc214

Requirements
Must have
• The web will exist in three possible languages in czech, english and deutsch.
• First page : introduction of a company
• Second page : Area of expertise
• Third page: servicies our company provides
• Fourth page: Our partners
• Fifth page: Conditions of our servicies
• Sixth page: Succesful projects
• - we would also love if we had possibility to add videos about our successful projects
• Seventh: Our team
• We are serious company in the sphere of funds and counsilary servicies, that is why we would love to have web design as representative as possible
• Take on mind that that we are specializing on development management, try to apply that on your design
• In the section of contacts, we would love to have photos of our team,
• This is our current site: http://www.pramenova-example.eu/cz/partneri.html
• This is how our concurency sites are lookin. Take these designs as an slight inspiration.
• http://www.lumatrava-example.sk/en/
• https://www2.brenvick-example.com/global/en.html
Nice to have
• Visible logo on the front page for the visitor.
• As a inspiration we provided link for our current web design, but we dont want to copy the current style, just look at the logo and the pages that exists on current web.
• !!!!!!We also uploaded file, where we explain how our cooperation with partner works. Especially in the part 2. section of service. Take that as an ispiration too, or use that to understand, what our company do.
Should not have
• We are serious company in the sphere of funds and counsilary servicies, that is why we would love to have web design representative as possible

```html
<!DOCTYPE html>
<html lang="en">
<head>
<meta charset="utf-8">
<title>Pramenova s.r.o. – Funds and Counsilary Services</title>
<link href="https://fonts.googleapis.com/css2?family=Open+Sans:wght@400;600;700&family=Raleway:wght@500;600;700&display=swap" rel="stylesheet">
<style>
:root{
  --green:#8dc63f;
  --green-light:#abd037;
  --green-mid:#9bcb3c;
  --yellow:#ffc214;
  --yellow-soft:#ffcf3e;
  --ink:#2b2b2b;
  --text:#555;
  --muted:#777;
  --grey-bg:#efefec;
  --line:#dcdcdc;
  --black:#050505;
  --white:#fff;
}
*{box-sizing:border-box;margin:0;padding:0}
html,body{width:1200px;height:4549px;overflow:hidden}
body{font-family:"Open Sans",sans-serif;color:var(--text);background:var(--white);position:relative}
section,header,footer,nav{position:absolute;left:0;width:1200px}
.abs{position:absolute}
.center{text-align:center;left:0;width:1200px}
h2{font-family:"Raleway",sans-serif;font-weight:700;color:var(--ink);font-size:30px;letter-spacing:.3px}
.btn{position:absolute;background:var(--yellow);color:var(--white);font-family:"Open Sans",sans-serif;font-weight:700;font-size:17px;display:flex;align-items:center;justify-content:center}
.arrow{position:absolute;color:#999;font-size:22px;line-height:1}

/* header */
.site-header{top:0;height:85px;background:var(--white)}
.brand{position:absolute;left:173px;top:27px;display:flex;align-items:center;gap:10px}
.brand-dot{width:14px;height:14px;border-radius:50%;background:var(--green)}
.brand-name{font-weight:600;font-size:18px;color:var(--ink)}
.site-footer .brand-name{color:var(--white)}
.header-phone{position:absolute;left:737px;top:24px;display:flex;align-items:center;gap:10px;font-size:15px;color:#444}
.phone-dot{width:32px;height:32px;border-radius:50%;background:var(--green);display:flex;align-items:center;justify-content:center}
.lang{position:absolute;left:925px;top:30px;font-size:15px;color:#444}
.lang::before{content:"|";position:absolute;left:-27px;color:#444}
.main-nav{top:85px;height:53px;background:#f3f3f3;display:flex;align-items:center;justify-content:center;gap:17px}
.main-nav a{font-size:10.5px;font-weight:600;color:#333;text-decoration:none;letter-spacing:.2px}

/* hero */
.hero{top:138px;height:511px;background:linear-gradient(100deg,#6d6a66 0%,#8f8a84 30%,#b9b5ad 55%,#8c7f70 75%,#a49a8d 100%)}
.hero-title{position:absolute;left:610px;top:140px;font-family:"Raleway",sans-serif;font-weight:700;font-size:64px;color:var(--white);letter-spacing:1px}
.hero-sub{position:absolute;left:612px;top:220px;font-weight:700;font-size:21px;color:var(--white)}
.dots{position:absolute;top:465px;left:571px;display:flex;gap:4px}
.dots span{width:11px;height:11px;border-radius:50%;border:1.5px solid var(--white)}
.dots span.on{background:var(--white)}

/* intro */
.intro{top:649px;height:387px}
.eyebrow{top:68px;font-size:12px;color:#555;letter-spacing:.5px}
.intro h2{top:96px}
.intro p{position:absolute;left:244px;top:143px;width:714px;text-align:center;font-size:12px;line-height:27px}

/* expertise */
.expertise{top:1036px;height:429px;background:linear-gradient(90deg,#e9e9e5,#f4f4f1 50%,#e7e7e3)}
.expertise h2{top:74px}
.expertise .lead{top:124px;font-size:12px}
.skill{position:absolute;top:173px;width:230px;text-align:center}
.skill-icon{width:88px;height:88px;border-radius:50%;background:var(--green);border:4px solid #f4f4f1;outline:2px solid var(--green);margin:0 auto 22px;display:flex;align-items:center;justify-content:center}
.skill h3{font-family:"Open Sans",sans-serif;font-weight:700;font-size:14px;color:var(--ink);margin-bottom:6px}
.skill p{font-size:11.5px;line-height:21px}

/* services */
.services{top:1465px;height:653px}
.services h2{top:64px}
.services .lead{top:116px;left:250px;width:700px;font-size:12px;line-height:24px;text-align:center}
.card{position:absolute;top:194px;width:276px;height:374px;border:2px solid #e3e3e3;background:var(--white)}
.card-photo{height:194px;margin:2px}
.card h3{font-weight:600;font-size:15px;color:#333;margin:30px 0 0 6px}
.card hr{width:30px;border:none;border-top:2px solid #bbb;margin:12px 0 14px 6px}
.card p{font-size:11.5px;line-height:25px;margin:0 6px}

/* partners */
.partners{top:2118px;height:333px;background:linear-gradient(170deg,#a9cf3a 0%,#93c33a 45%,#9fcb38 70%,#86b831 100%)}
.partners h2{top:68px;color:var(--white)}
.partner{position:absolute;top:137px;width:254px;height:106px;background:var(--white);border-radius:3px;display:flex;align-items:center;justify-content:center}
.partner .badge{border-radius:4px}
.partners .arrow{color:var(--white)}

/* conditions */
.conditions{top:2451px;height:570px}
.conditions h2{position:absolute;left:171px;top:95px;line-height:42px}
.conditions p{position:absolute;left:171px;width:441px;font-size:12.5px;line-height:27px}
.cond-frame{position:absolute;left:715px;top:92px;width:310px;height:357px;background:var(--green-light)}
.cond-photo{position:absolute;left:683px;top:110px;width:326px;height:356px;background:linear-gradient(160deg,#cfd0cd,#8c8c88 45%,#5b5a55 70%,#8a6f50)}

/* projects */
.projects{top:3021px;height:561px;background:linear-gradient(180deg,#f4f4f4,#eeeeee)}
.projects h2{top:74px}
.projects .lead{top:125px;font-size:12.5px}
.tile{position:absolute;width:205px;height:146px;display:flex;align-items:center;justify-content:center}
.play{width:40px;height:40px;border-radius:50%;border:2px solid var(--white);display:flex;align-items:center;justify-content:center}

/* team */
.team{top:3582px;height:638px}
.team h2{top:78px}
.team .lead{top:131px;font-size:12.5px}
.team-photo{position:absolute;left:213px;top:172px;width:772px;height:393px;border:1px solid #ddd;background:linear-gradient(180deg,#f3f3f3 0%,#dcdcdc 45%,#2e3440 80%,#1f242e 100%)}

/* footer */
.site-footer{top:4220px;height:329px;background:var(--black);color:#ddd}
.footer-brand{position:absolute;left:171px;top:84px;display:flex;align-items:center;gap:10px}
.social{position:absolute;top:156px;left:183px;display:flex;gap:16px}
.social span{width:30px;height:30px;border-radius:50%;border:1.5px solid #ddd}
.footer-col h4{position:absolute;top:56px;font-weight:400;font-size:17px;color:var(--white)}
.contact-item{position:absolute;left:494px;display:flex;gap:12px;font-size:11.5px;line-height:20px;color:#ddd}
.contact-item svg{margin-top:4px;flex:none}
.field{position:absolute;left:801px;width:226px;height:30px;background:var(--white);font-size:10.5px;color:#888;padding:7px 12px}
.join{position:absolute;left:801px;top:176px;width:85px;height:28px;border:1.5px solid #ddd;color:var(--white);font-size:11.5px;font-weight:600;display:flex;align-items:center;justify-content:center}
.footer-rule{position:absolute;left:171px;top:263px;width:856px;border-top:1px solid #444}
.copyright{position:absolute;top:290px;left:0;width:1200px;text-align:center;font-size:11.5px;color:#ccc}
</style>
</head>
<body>

<header class="site-header">
  <div class="brand"><span class="brand-dot"></span><span class="brand-name">Pramenova s.r.o.</span></div>
  <div class="header-phone">
    <span class="phone-dot"><svg width="15" height="15" viewBox="0 0 24 24"><path fill="#fff" d="M6.6 10.8a15 15 0 0 0 6.6 6.6l2.2-2.2c.3-.3.7-.4 1-.2 1.1.4 2.3.6 3.6.6.6 0 1 .4 1 1V20c0 .6-.4 1-1 1A17 17 0 0 1 3 4c0-.6.4-1 1-1h3.5c.6 0 1 .4 1 1 0 1.3.2 2.5.6 3.6.1.3 0 .7-.2 1z"/></svg></span>
    (+1) 555 010 0199
  </div>
  <div class="lang">Lan: Eng <svg width="9" height="6" viewBox="0 0 10 6"><path d="M1 1l4 4 4-4" stroke="#444" stroke-width="1.5" fill="none"/></svg></div>
</header>

<nav class="main-nav">
  <a href="#">INTRODUCTION OF A COMPANY</a>
  <a href="#">AREA OF EXPERTISE</a>
  <a href="#">SERVICES</a>
  <a href="#">OUR PARTNERS</a>
  <a href="#">CONDITIONS OF OUR SERVICES</a>
  <a href="#">SUCCESSFUL PROJECTS</a>
  <a href="#">OUR TEAM</a>
</nav>

<section class="hero" role="img" aria-label="Photo of the company office building and car park">
  <div class="hero-title">PRAMENOVA</div>
  <div class="hero-sub">Funds and Counsilary Services</div>
  <div class="btn" style="left:612px;top:280px;width:122px;height:37px">Read More</div>
  <div class="dots"><span class="on"></span><span></span><span></span><span></span></div>
</section>

<section class="intro">
  <div class="abs center eyebrow">WELCOME TO</div>
  <h2 class="abs center">INTRODUCTION OF A COMPANY</h2>
  <p>Lorem ipsum dolor sit amet, consectetur adipiscing elit, sed do eiusmod tempor incididunt ut labore et dolore magna aliqua. Ut enim ad minim veniam, quis nostrud exercitation ullamco laboris nisi ut aliquip ex ea commodo consequat. Duis aute irure dolor sed ut perspiciatis unde omnis iste natus error sit voluptatem accusantium doloremque laudantium, totam in reprehenderit in voluptate velit esse cillum dolore eu fugiat nulla pariatur qui officia deserunt mollit dolores.</p>
  <div class="btn" style="left:531px;top:267px;width:136px;height:41px">Read More</div>
</section>

<section class="expertise">
  <h2 class="abs center">AREA OF EXPERTISE</h2>
  <div class="abs center lead">Lorem ienimini veniam, quis nostrud exercitation ullamco laborist aliquip exaeuts</div>
  <span class="arrow" style="left:152px;top:230px">‹</span>
  <span class="arrow" style="left:1036px;top:230px">›</span>
  <div class="skill" style="left:173px">
    <div class="skill-icon"><svg width="40" height="36" viewBox="0 0 40 36"><path d="M4 14L20 4l16 10v20H4z" fill="#fff"/><rect x="11" y="18" width="18" height="16" fill="#8dc63f"/><path d="M13 22h14M13 26h14M13 30h14" stroke="#fff" stroke-width="2"/></svg></div>
    <h3>Lorem Ipsum Is Simple</h3>
    <p>Amet suspendisse pede. Adipiscing lacus dictumst. Eu in est pellentesque varius magnis ut mi diam.</p>
  </div>
  <div class="skill" style="left:485px">
    <div class="skill-icon"><svg width="46" height="30" viewBox="0 0 46 30"><rect x="2" y="4" width="26" height="18" fill="#fff"/><path d="M30 10h8l6 7v5H30z" fill="#fff"/><circle cx="10" cy="25" r="4" fill="#fff" stroke="#8dc63f" stroke-width="2"/><circle cx="36" cy="25" r="4" fill="#fff" stroke="#8dc63f" stroke-width="2"/></svg></div>
    <h3>Lorem Ipsum Is Simple</h3>
    <p>Amet suspendisse pede. Adipiscing lacus dictumst. Eu in est pellentesque varius magnis ut mi diam.</p>
  </div>
  <div class="skill" style="left:796px">
    <div class="skill-icon"><svg width="40" height="38" viewBox="0 0 40 38"><path d="M3 16L20 3l17 13" stroke="#fff" stroke-width="3" fill="none"/><rect x="8" y="16" width="24" height="20" fill="none" stroke="#fff" stroke-width="3"/><rect x="15" y="22" width="10" height="14" fill="#fff"/></svg></div>
    <h3>Lorem Ipsum Is Simple</h3>
    <p>Amet suspendisse pede. Adipiscing lacus dictumst. Eu in est pellentesque varius magnis ut mi diam.</p>
  </div>
</section>

<section class="services">
  <h2 class="abs center">SERVICES OUR COMPANY PROVIDES</h2>
  <p class="abs lead">Lorem ipsum dolor sit amet, consectetur adipiscing elit, sed do eiusmod tempor incididunt ut labore et dolore magna aliqua. Ut enim ad minim veniam, quis nostrud exercitation occaecat cupidatat.</p>
  <span class="arrow" style="left:122px;top:354px;font-size:30px">‹</span>
  <span class="arrow" style="left:1062px;top:354px;font-size:30px">›</span>
  <article class="card" style="left:171px">
    <div class="card-photo" role="img" aria-label="Photo of people reviewing charts at a desk" style="background:linear-gradient(150deg,#e8e6e3,#cfcac4 60%,#e6a25a)"></div>
    <h3>Project coordination</h3><hr>
    <p>Lorem Ipsum is simply dummy text of the printing . Lorems has been the industry's dummy text ever since 1500s....</p>
  </article>
  <article class="card" style="left:459px">
    <div class="card-photo" role="img" aria-label="Photo of a budget binder, calculator and financial sheets" style="background:linear-gradient(150deg,#1f3f73,#4a6da0 40%,#dfe3ea 75%)"></div>
    <h3>Project Financing</h3><hr>
    <p>Lorem Ipsum is simply dummy text of the printing . Lorems has been the industry's dummy text ever since 1500s....</p>
  </article>
  <article class="card" style="left:752px">
    <div class="card-photo" role="img" aria-label="Photo of a businessman holding a glowing world map" style="background:radial-gradient(circle at 55% 45%,#6f8090,#2a3138 55%,#15191d)"></div>
    <h3>Export Promotion</h3><hr>
    <p>Lorem Ipsum is simply dummy text of the printing . Lorems has been the industry's dummy text ever since 1500s....</p>
  </article>
</section>

<section class="partners">
  <h2 class="abs center">OUR PARTNERS</h2>
  <span class="arrow" style="left:126px;top:181px">‹</span>
  <span class="arrow" style="left:1061px;top:181px">›</span>
  <div class="partner" style="left:194px"><span class="badge" style="width:170px;height:40px;background:#c8102e"></span></div>
  <div class="partner" style="left:473px"><span class="badge" style="width:140px;height:50px;background:#1d3c8f"></span></div>
  <div class="partner" style="left:750px"><span class="badge" style="width:210px;height:40px;background:#44546a"></span></div>
</section>

<section class="conditions">
  <h2>CONDITIONS<br>OF OUR SERVICES</h2>
  <p style="top:196px">Sed ut perspiciatis unde omnis iste natus error sit voluptatem accuo santium doloremque laudantium, totam rem aperiam, eaque ipsa quae ab illo inventore veritatis et quasi architecto beatae vitae dicta sunt explicabo. Nemo enim ipsam voluptatem quia voluptas sit aspera natur aut odit aut fugit, sed quia consequuntur.</p>
  <p style="top:343px">Samagni dolores eos qui ratione voluptatem sequi nesciunt. Neque porro quisquam est, qui dolorem ipsum quia dolor sit amet, consectes tur dolor.</p>
  <div class="btn" style="left:171px;top:434px;width:138px;height:42px">Read More</div>
  <div class="cond-frame"></div>
  <div class="cond-photo" role="img" aria-label="Photo of a wood processing production line in a factory hall"></div>
</section>

<section class="projects">
  <h2 class="abs center">SUCCESSFUL PROJECTS</h2>
  <div class="abs center lead">Duis aute irure dolor in reprehenderit in voluptate velit esse</div>
  <div class="tile" style="left:171px;top:177px;background:linear-gradient(180deg,#8fb0d6,#c9c9c4 55%,#7b7b76)" role="img" aria-label="Video of a new industrial hall"><span class="play"><svg width="12" height="14" viewBox="0 0 12 14"><path d="M1 1l10 6-10 6z" fill="#fff"/></svg></span></div>
  <div class="tile" style="left:390px;top:177px;background:linear-gradient(180deg,#a9c2de,#bdb5aa 50%,#8f8a82)" role="img" aria-label="Photo of a renovated office building"></div>
  <div class="tile" style="left:607px;top:177px;background:linear-gradient(180deg,#d8dde2,#9aa08c 55%,#4e5340)" role="img" aria-label="Video of forestry machinery at a site"><span class="play"><svg width="12" height="14" viewBox="0 0 12 14"><path d="M1 1l10 6-10 6z" fill="#fff"/></svg></span></div>
  <div class="tile" style="left:822px;top:177px;background:linear-gradient(180deg,#7ea6d4,#d9c7b7 50%,#9d8c7c)" role="img" aria-label="Photo of a residential building project"></div>
  <div class="tile" style="left:171px;top:336px;background:linear-gradient(160deg,#b8b6b0,#6f6a62 55%,#4b4640)" role="img" aria-label="Photo of woodworking machinery"></div>
  <div class="tile" style="left:390px;top:336px;background:linear-gradient(160deg,#e9e9e9,#8a8a8a 50%,#3a3a3a)" role="img" aria-label="Video of precision machine equipment"><span class="play"><svg width="12" height="14" viewBox="0 0 12 14"><path d="M1 1l10 6-10 6z" fill="#fff"/></svg></span></div>
  <div class="tile" style="left:607px;top:336px;background:linear-gradient(180deg,#3f73c2,#6e9ad6 40%,#c07a45 70%,#9a5f36)" role="img" aria-label="Photo of stacked timber at a lumber yard"></div>
  <div class="tile" style="left:822px;top:336px;background:linear-gradient(180deg,#f2f2ee,#e0ddd4 60%,#c9c3b4)" role="img" aria-label="Video of a laboratory interior"><span class="play"><svg width="12" height="14" viewBox="0 0 12 14"><path d="M1 1l10 6-10 6z" fill="#fff"/></svg></span></div>
</section>

<section class="team">
  <h2 class="abs center">OUR TEAM</h2>
  <div class="abs center lead">Duis aute irure dolor in reprehenderit in voluptate velit esse</div>
  <div class="team-photo" role="img" aria-label="Group photo of the company team in business attire"></div>
</section>

<footer class="site-footer">
  <div class="footer-brand"><span class="brand-dot"></span><span class="brand-name">Pramenova s.r.o.</span></div>
  <div class="social"><span></span><span></span><span></span><span></span></div>

  <div class="footer-col"><h4 style="left:494px">Contact Us</h4></div>
  <div class="contact-item" style="top:96px"><svg width="9" height="12" viewBox="0 0 10 14"><path d="M5 0a5 5 0 0 0-5 5c0 4 5 9 5 9s5-5 5-9a5 5 0 0 0-5-5zm0 7a2 2 0 1 1 0-4 2 2 0 0 1 0 4z" fill="#ddd"/></svg><span>Pramenova sro,<br>Lorem Ipsum Is Simple.</span></div>
  <div class="contact-item" style="top:145px"><svg width="10" height="10" viewBox="0 0 24 24"><path fill="#ddd" d="M6.6 10.8a15 15 0 0 0 6.6 6.6l2.2-2.2c.3-.3.7-.4 1-.2 1.1.4 2.3.6 3.6.6.6 0 1 .4 1 1V20c0 .6-.4 1-1 1A17 17 0 0 1 3 4c0-.6.4-1 1-1h3.5c.6 0 1 .4 1 1 0 1.3.2 2.5.6 3.6.1.3 0 .7-.2 1z"/></svg><span>+1 555-010-0199</span></div>
  <div class="contact-item" style="top:179px"><svg width="10" height="8" viewBox="0 0 12 9"><rect width="12" height="9" fill="#ddd"/><path d="M0 0l6 5 6-5" stroke="#050505" fill="none"/></svg><span>info@pramenova-example.com</span></div>

  <div class="footer-col"><h4 style="left:801px">Newsletter sign up</h4></div>
  <div class="field" style="top:95px">Name</div>
  <div class="field" style="top:134px">Enter email</div>
  <div class="join">JOIN US</div>

  <div class="footer-rule"></div>
  <div class="copyright">Copyright © 2019. All Rights Reserved</div>
</footer>

</body>
</html>
```